Islamic App which helps to calculate, track and pay Zakat

We need an application which helps muslim people to calculate and pay Zakat - mandatory donations which muslim should pay based on his income. The application will consist of two parts (applications) - the one which is used by "payer" and another one - used by "receiver". To make a payment "payer" will scan QR-code which "receiver" will generate in his app and show to payer. "Receiver" will have option to initiate cash withdrawal once he collected required minimum for the withdrawal.
Important that "payer" side journey to make a payment should be as short as possible - imaging same as you make donation by cash - you just gave money and left, similar experience should be with app - couple-three taps to make it. For receiver side major requirement is to keep the UI/UX as simple as possible, these guys usually are not aware about online payments (roughly speaking this part of the app should be more similar to Quillotap rather than to banking/financial app)
In this Figma I tried to sketch the UX for both sides (just to explain the idea): https://www.plovix.com/file/Rt4mWq8ZpLbN2vKe7sJd3X/Plovix-basics?type=design&node-id=2741-583016&mode=design

Target Market(s)

Muslims

Industry/Entity Type

Donations

Colors
0094D4
00A9DD
6FCCEA
C7EBF8
E9F6FB
00AB8E
00BBA5
67D7C9
C6EFE9
E9F9F6

Requirements
Must have
• The application should have soul. Design should show that this application intend to help people, not just money transfer
Nice to have
• Payment should be as quick as possible, in the sketches I showed it as banknotes/coins which user need to slide-up to pay. Maybe make it similar as Vel OS dock icons?
Should not have
• The application should not look as banking/financial app or wallet app

```html
<!DOCTYPE html>
<html lang="en">
<head>
<meta charset="utf-8">
<title>Amanah – Zakat App Screens</title>
<link href="https://fonts.googleapis.com/css2?family=Work+Sans:wght@400;500;600;700&display=swap" rel="stylesheet">
<style>
  :root{
    --bg:#d9fbf8;
    --teal:#1fb4a0;
    --teal-deep:#17a18f;
    --teal-soft:#67d7c9;
    --white:#ffffff;
    --ink:#3e4347;
    --ink-strong:#2b2f33;
    --muted:#8a9096;
    --faint:#c3c8cc;
    --line:#e4e7e9;
    --pad:#eef2f2;
    --photo-sky:#a7a39a;
    --photo-city:#8a5d45;
    --photo-stone:#c49a6a;
  }
  *{box-sizing:border-box;margin:0;padding:0}
  html,body{width:1200px;height:727px;overflow:hidden}
  body{background:var(--bg);font-family:"Work Sans",sans-serif;color:var(--ink);position:relative}
  .screen{position:absolute;top:93px;width:262px;height:568px;border-radius:30px;background:var(--white);overflow:hidden;box-shadow:0 18px 40px rgba(40,120,110,.18)}
  .screen--signin{left:113px}
  .screen--code{left:482px}
  .screen--profile{left:850px}

  .header{position:absolute;left:0;top:0;width:100%;height:200px}
  .brand{position:absolute;left:0;top:58px;width:100%;text-align:center;color:var(--white)}
  .brand__dot{width:38px;height:38px;border-radius:50%;background:var(--white);margin:0 auto 10px}
  .brand__name{font-size:24px;font-weight:500;letter-spacing:.5px}
  .chevron{position:absolute;left:116px;top:171px;width:30px;height:30px;border-radius:50%;background:var(--teal);box-shadow:0 3px 8px rgba(0,0,0,.18);display:flex;align-items:center;justify-content:center}

  .title{position:absolute;left:0;width:100%;text-align:center;font-size:20px;font-weight:600;color:var(--ink);line-height:27px}
  .btn{position:absolute;left:50%;transform:translateX(-50%);width:97px;height:25px;border-radius:5px;background:var(--teal);color:var(--white);font-size:13px;font-weight:500;display:flex;align-items:center;justify-content:center;box-shadow:0 2px 5px rgba(23,161,143,.3)}

  .phone-field{position:absolute;left:46px;top:300px;width:172px;font-size:16.5px;font-weight:500;color:var(--ink-strong);border-bottom:1px solid var(--line);padding-bottom:6px;white-space:nowrap}
  .phone-field span{color:var(--faint);font-weight:400}
  .helper{position:absolute;left:46px;top:335px;font-size:7.6px;color:var(--muted)}

  .sms-note{position:absolute;left:0;top:258px;width:100%;text-align:center;font-size:8.2px;line-height:12px;color:var(--muted)}
  .sms-note b{color:var(--ink-strong);font-weight:500}
  .code-row{position:absolute;left:77px;top:298px;display:flex;gap:8px}
  .code-cell{width:22px;text-align:center;font-size:16px;color:var(--faint);border-bottom:1px solid var(--line);padding-bottom:5px}

  .keypad{position:absolute;left:0;top:425px;width:100%;height:143px;background:var(--pad);padding:16px 15px 0;display:grid;grid-template-columns:repeat(3,67px);column-gap:15px;row-gap:6px}
  .key{height:21px;background:var(--white);border-radius:4px;display:flex;align-items:center;justify-content:center;gap:5px;font-size:11px;color:var(--ink-strong);box-shadow:0 1px 1px rgba(0,0,0,.05)}
  .key small{font-size:6px;color:var(--ink)}

  .photo{position:absolute;left:0;top:0;width:100%;height:372px;background:linear-gradient(180deg,var(--photo-sky) 0%,#9c8e7c 30%,var(--photo-city) 48%,var(--photo-stone) 75%,#b07a52 100%)}
  .round-btn{position:absolute;top:44px;width:25px;height:25px;border-radius:50%;background:var(--white);display:flex;align-items:center;justify-content:center}
  .card{position:absolute;left:0;top:362px;width:100%;height:206px;background:var(--white);border-radius:22px 22px 0 0}
  .name{position:absolute;left:15px;top:22px;font-size:19px;font-weight:600;color:var(--ink-strong)}
  .intro{position:absolute;left:16px;top:56px;font-size:10.3px;color:var(--ink)}
  .story{position:absolute;left:16px;top:78px;width:225px;font-size:11.2px;line-height:17.5px;color:var(--muted)}
  .amount{position:absolute;left:16px;top:151px;font-size:27px;font-weight:600;color:var(--ink-strong)}
  .amount span{font-size:16px;font-weight:500;color:var(--ink);margin-left:4px}
  .pay-btn{position:absolute;left:217px;top:153px;width:30px;height:28px;border-radius:5px;background:var(--teal);display:flex;align-items:center;justify-content:center}
</style>
</head>
<body>

<section class="screen screen--signin">
  <svg class="header" viewBox="0 0 262 200" aria-hidden="true"><path d="M0 0H262V190C248 178 232 176 190 176C162 176 150 160 131 160C112 160 100 176 72 176C30 176 14 178 0 190Z" fill="var(--teal)"/></svg>
  <div class="brand"><div class="brand__dot"></div><div class="brand__name">Amanah</div></div>
  <div class="chevron"><svg width="12" height="8" viewBox="0 0 12 8"><path d="M1 1.5L6 6.5L11 1.5" fill="none" stroke="#fff" stroke-width="1.6" stroke-linecap="round"/></svg></div>
  <h1 class="title" style="top:230px">Sign in<br>to Amanah App</h1>
  <div class="phone-field">+971 <span>(50) 000-00-00</span></div>
  <p class="helper">Please enter your UAE phone number</p>
  <div class="btn" style="top:367px">Next</div>
  <div class="keypad">
    <div class="key">1 <small>ABC</small></div><div class="key">2 <small>DEF</small></div><div class="key">3 <small>GHI</small></div>
    <div class="key">4 <small>JKL</small></div><div class="key">5 <small>MNO</small></div><div class="key">6 <small>PQR</small></div>
    <div class="key">7 <small>STU</small></div><div class="key">8 <small>VWX</small></div><div class="key">9 <small>YZ</small></div>
    <div class="key"><small>+ * #</small></div><div class="key">0</div><div class="key"><svg width="12" height="8" viewBox="0 0 12 8"><path d="M3.5 .5H11.5V7.5H3.5L.5 4Z M6 2.5L9 5.5M9 2.5L6 5.5" fill="none" stroke="#555" stroke-width=".8"/></svg></div>
  </div>
</section>

<section class="screen screen--code">
  <svg class="header" viewBox="0 0 262 200" aria-hidden="true"><path d="M0 0H262V190C248 178 232 176 190 176C162 176 150 160 131 160C112 160 100 176 72 176C30 176 14 178 0 190Z" fill="var(--teal)"/></svg>
  <div class="brand"><div class="brand__dot"></div><div class="brand__name">Amanah</div></div>
  <div class="chevron"><svg width="12" height="8" viewBox="0 0 12 8"><path d="M1 1.5L6 6.5L11 1.5" fill="none" stroke="#fff" stroke-width="1.6" stroke-linecap="round"/></svg></div>
  <h1 class="title" style="top:230px">Input Code</h1>
  <p class="sms-note">We have sent an SMS with a 4-digit code to<br>phone <b>+971 50 0004821</b></p>
  <div class="code-row"><div class="code-cell">0</div><div class="code-cell">0</div><div class="code-cell">0</div><div class="code-cell">0</div></div>
  <div class="btn" style="top:354px">Sign In</div>
  <div class="keypad">
    <div class="key">1 <small>ABC</small></div><div class="key">2 <small>DEF</small></div><div class="key">3 <small>GHI</small></div>
    <div class="key">4 <small>JKL</small></div><div class="key">5 <small>MNO</small></div><div class="key">6 <small>PQR</small></div>
    <div class="key">7 <small>STU</small></div><div class="key">8 <small>VWX</small></div><div class="key">9 <small>YZ</small></div>
    <div class="key"><small>+ * #</small></div><div class="key">0</div><div class="key"><svg width="12" height="8" viewBox="0 0 12 8"><path d="M3.5 .5H11.5V7.5H3.5L.5 4Z M6 2.5L9 5.5M9 2.5L6 5.5" fill="none" stroke="#555" stroke-width=".8"/></svg></div>
  </div>
</section>

<section class="screen screen--profile">
  <div class="photo" role="img" aria-label="Aerial photo of a historic tiled mosque among dense city rooftops"></div>
  <div class="round-btn" style="left:16px"><svg width="11" height="11" viewBox="0 0 11 11"><path d="M1.5 9.5L2 7.5L7.5 2L9 3.5L3.5 9Z" fill="var(--teal)"/></svg></div>
  <div class="round-btn" style="left:221px"></div>
  <div class="card">
    <h2 class="name">Kareem</h2>
    <p class="intro">I am from Pakistan. I have three kids.</p>
    <p class="story">Lorem ipsum doloret, consectetur adipiscing elit, sed do eiusmod tempor inc labore et dolore magn.</p>
    <div class="amount">847<span>AED</span></div>
    <div class="pay-btn"><svg width="16" height="15" viewBox="0 0 16 15"><rect x="1" y="1" width="14" height="4" rx="1" fill="none" stroke="#fff" stroke-width="1.4"/><rect x="3.5" y="5" width="9" height="9" rx="1" fill="none" stroke="#fff" stroke-width="1.4"/><path d="M8 6.5V11.5M6 9.5L8 11.5L10 9.5" fill="none" stroke="#fff" stroke-width="1.3"/></svg></div>
  </div>
</section>

</body>
</html>
```